Medical centre needs a business card

We are a medcial centre in Australia, needing a new business card. Our demographic is low working class families. We are going to be renovating our premises to modernise the look and also had a new logo done a few months ago representing quality and community, and now need to update our cards. It needs to be doubled sided, with logo and contact details on the front, and appointment details on the back. . Needs to be modern and simple, easy to read. <br/><br/>Name: Kindle Grove Medical Centre <br/>Address: 512 Parmley Rd (Cnr Parmley Rd & Osgood Creek Rd),<br/>Tindarra Court Shopping Centre, Paralowie, SA 5108<br/>Ph: 08 8461 3072<br/>Tag line: Where your wellbeing comes first<br/>Website: www.kindlegrovemedicalcentre-example.com.au<br/>Online bookings also available<br/><br/>(On the back, to have 3 lines of appointments that can be written in.<br/>Day, date, time)<br/><br/>Your next appointment is on<br/>Can try “M T W Th F Sa Su _________________ at ____________ am/pm” or other combinations <br/>Please advise as soon as possible if unable to attend<br/>Cancellation fees apply if less than 2 hrs notice<br/>Online appointments available (please highlight this option by either by position, colour or font)

Target Market(s)

Lower social economic working class, young families to seniors

Industry/Entity Type

Medical Centre

Contact Information for Business Card

Kindle Grove Medical Centre
512 Parmley Rd (Cnr Parmley Rd & Osgood Creek Drive)
Tindarra Court Shopping Centre
Marlow Heights SA 5192
Ph: 08 8461 3072
www.kindlegrovemedicalcentre-example.com.au
Tagline line: where your wellbeing comes first
Back side is for appointments
Your next appointment is with Dr ______________
Day/date/time (Please give 3 lines of appointments)
Please advise as soon as possible if unable to attend
Cancellation fees apply if less than 2 hours notice
Online appointments available
Book online easily and conveniently (please highlight online appointments)

Font styles to use
Serif
Sans Serif

Colors

Designer to choose colors to be used in the design.

Requirements
Must have
• Modern and simple
• Easy to ready
• Induces a wellbeing feeling
• Incorporate our logo colours and feel from logo
• Induces feeling of stability and security
Nice to have
• Attract attention
• Pleasant to look at
• Feeling of innovation
Should not have
• Loud clashing colours
• Overly luxurious feeling
• Overly artistic

```html
<!DOCTYPE html>
<html lang="en">
<head>
<meta charset="utf-8">
<title>Kindle Grove Medical Centre – Business Card</title>
<link href="https://fonts.googleapis.com/css2?family=Open+Sans:wght@400;600;700&display=swap" rel="stylesheet">
<style>
  :root{
    --brand-blue:#1273bd;
    --brand-green:#8cc63f;
    --ink:#2b2b2b;
    --rule:#555;
    --stage:#2b2b2b;
    --card:#ffffff;
  }
  *{box-sizing:border-box;margin:0;padding:0}
  html,body{width:1200px;height:1021px;overflow:hidden;background:var(--stage)}
  body{font-family:"Open Sans",Arial,sans-serif;color:var(--ink);position:relative}
  .card{position:absolute;left:220px;width:760px;height:465px;background:var(--card);overflow:hidden}
  .card--back{top:30px}
  .card--front{top:526px}

  /* Back: appointment side */
  .appt-title{position:absolute;top:34px;left:0;right:0;text-align:center;color:var(--brand-blue);font-weight:700;font-size:24px;letter-spacing:.5px}
  .field{position:absolute;display:flex;align-items:flex-end;font-size:19px}
  .field .line{flex:1;border-bottom:1.5px solid var(--rule);margin:0 10px 5px 8px;height:1px}
  .field--doctor{top:82px;left:48px;right:48px}
  .days{position:absolute;top:134px;left:48px;right:36px;display:flex;justify-content:space-between;font-size:19px}
  .day{display:flex;align-items:center;gap:8px}
  .box{width:22px;height:20px;border:2px solid var(--brand-green)}
  .appt-row{position:absolute;left:48px;right:36px;display:flex;align-items:flex-end;font-size:19px}
  .appt-row .line{border-bottom:1.5px solid var(--rule);margin:0 10px 5px 8px}
  .appt-row .date{flex:1.6}
  .appt-row .time{flex:1}
  .notice{position:absolute;top:336px;left:0;right:0;text-align:center;font-size:19px;line-height:1.35}
  .online{position:absolute;top:404px;left:0;right:0;text-align:center;font-size:19px}
  .online .hl{color:var(--brand-green);font-weight:600}
  .online .sub{color:var(--brand-blue)}

  /* Front: contact side */
  .edge-band{position:absolute;left:0;top:0;width:36px;height:465px}
  .brand{position:absolute;top:66px;left:92px;display:flex;align-items:center;gap:12px}
  .brand-mark{width:26px;height:26px;background:var(--brand-blue)}
  .brand-name{color:var(--brand-blue);font-weight:700;font-size:26px;line-height:1.1;width:220px}
  .tagline{position:absolute;top:150px;right:50px;font-size:21px;font-weight:600}
  .tagline .g{color:var(--brand-green)}
  .tagline .b{color:var(--brand-blue)}
  .person{position:absolute;top:212px;left:92px}
  .person-name{color:var(--brand-blue);font-weight:600;font-size:27px}
  .person-role{font-size:20px;margin-top:-2px}
  .contact{position:absolute;right:50px;top:236px;text-align:right;font-size:20px;line-height:1.3;font-style:normal}
  .contact .org{color:var(--brand-blue);font-size:21px;margin-bottom:4px}
  .contact .row{display:flex;justify-content:flex-end;align-items:center;gap:8px}
  .contact .gap{margin-top:8px}
  .icon{width:18px;height:18px;flex:none}
</style>
</head>
<body>

<section class="card card--back" aria-label="Appointment side">
  <h2 class="appt-title">YOUR NEXT APPOINTMENT</h2>
  <div class="field field--doctor"><span>Dr.:</span><span class="line"></span></div>
  <div class="days">
    <span class="day"><span class="box"></span>Mon</span>
    <span class="day"><span class="box"></span>Tue</span>
    <span class="day"><span class="box"></span>Wed</span>
    <span class="day"><span class="box"></span>Thu</span>
    <span class="day"><span class="box"></span>Fri</span>
    <span class="day"><span class="box"></span>Sat</span>
    <span class="day"><span class="box"></span>Sun</span>
  </div>
  <div class="appt-row" style="top:190px"><span>Date:</span><span class="line date"></span><span>Time:</span><span class="line time"></span><span>am/pm</span></div>
  <div class="appt-row" style="top:236px"><span>Date:</span><span class="line date"></span><span>Time:</span><span class="line time"></span><span>am/pm</span></div>
  <div class="appt-row" style="top:282px"><span>Date:</span><span class="line date"></span><span>Time:</span><span class="line time"></span><span>am/pm</span></div>
  <p class="notice">Please advise as soon as possible if unable to attend<br>Cancellation fees apply if less than 2 hours notice</p>
  <p class="online"><span class="hl">Online appointments available</span> <span class="sub">| Book online easily and conveniently</span></p>
</section>

<section class="card card--front" aria-label="Contact side">
  <svg class="edge-band" viewBox="0 0 36 465" preserveAspectRatio="none" aria-hidden="true">
    <polygon points="0,0 36,0 36,225 0,265" fill="#1273bd"/>
    <polygon points="0,265 36,225 36,465 0,465" fill="#8cc63f"/>
  </svg>
  <div class="brand">
    <span class="brand-mark"></span>
    <span class="brand-name">Kindle Grove Medical Centre</span>
  </div>
  <p class="tagline"><span class="g">Where Your Wellbeing</span> <span class="b">Comes First</span></p>
  <div class="person">
    <p class="person-name">Daniel Harlow</p>
    <p class="person-role">Founder</p>
  </div>
  <address class="contact">
    <p class="org">Kindle Grove Medical Centre</p>
    <p>512 Parmley Rd</p>
    <p>(Cnr Parmley Rd &amp; Osgood Creek Drive)</p>
    <p>Tindarra Court Shopping Centre</p>
    <p>Marlow Heights SA 5192</p>
    <p class="row gap">08 8461 3072
      <svg class="icon" viewBox="0 0 24 24" aria-hidden="true"><path fill="#8cc63f" d="M6.6 10.8a15.1 15.1 0 0 0 6.6 6.6l2.2-2.2c.3-.3.7-.4 1-.2 1.1.4 2.3.6 3.6.6.6 0 1 .4 1 1V20c0 .6-.4 1-1 1A17 17 0 0 1 3 4c0-.6.4-1 1-1h3.5c.6 0 1 .4 1 1 0 1.3.2 2.5.6 3.6.1.3 0 .7-.2 1z"/></svg>
    </p>
    <p class="row">www.kindlegrovemedicalcentre-example.com.au
      <svg class="icon" viewBox="0 0 24 24" aria-hidden="true" fill="none" stroke="#8cc63f" stroke-width="2"><circle cx="12" cy="12" r="9"/><ellipse cx="12" cy="12" rx="4" ry="9"/><path d="M3 12h18M5 7h14M5 17h14"/></svg>
    </p>
  </address>
</section>

</body>
</html>
```